We are a local Communty Pharmacy wishing to promote and market a specialised Pharmaceutical Service

We would like a design that is professional and enticing ( according to the brief In attached files)
We wish to Market Compounding Pharmacy as a specialist side of our business.
We have the expertise a purpose built preparation laboratory.
The main purpose is an Internet presence that entices prospective patients to contact or visit our physical store.

Target Market(s)

Patients Medicos and Veterinary clients

Industry/Entity Type

Pharmacy

Coding

Coded - Design and coding required

Number of Pages Required

1 page

Requirements
Must have
• Clear friendly image
Nice to have
• soft enticing feel
Should not have
• No crass loud unprofessional elements

```html
<!DOCTYPE html>
<html lang="en">
<head>
<meta charset="utf-8">
<title>Compounding Pharmacy</title>
<link href="https://fonts.googleapis.com/css2?family=Open+Sans:wght@400;600;700&display=swap" rel="stylesheet">
<style>
:root{
  --sky:#6ccbe9;
  --teal:#3aa6cf;
  --ink:#333a40;
  --muted:#7d858c;
  --white:#ffffff;
  --panel:#eef0f2;
  --dark-btn:#3c4247;
}
*{box-sizing:border-box;margin:0;padding:0}
html,body{width:771px;height:1200px;overflow:hidden;background:var(--white)}
body{font-family:"Open Sans",Arial,sans-serif;color:var(--ink);position:relative}
.topbar{height:20px;background:var(--sky);color:var(--white);font-size:8px;display:flex;justify-content:space-between;align-items:center;padding:0 64px}
.header{height:83px;display:flex;justify-content:space-between;align-items:center;padding:0 64px}
.brand{display:flex;align-items:center;gap:10px}
.brand-dot{width:30px;height:30px;border-radius:50%;background:var(--teal)}
.brand-name{font-size:19px;font-weight:600;color:var(--teal);line-height:1.05}
.nav{display:flex;gap:26px;font-size:10px;color:var(--ink)}
.hero{position:relative;height:295px}
.hero-photo{position:absolute;inset:0;
  background:
    radial-gradient(ellipse 150px 190px at 83% 62%,#ffffff 0%,rgba(255,255,255,.85) 45%,rgba(255,255,255,0) 100%),
    radial-gradient(ellipse 70px 70px at 82% 22%,#d7b49c 0%,rgba(215,180,156,0) 100%),
    radial-gradient(ellipse 90px 110px at 55% 45%,rgba(250,250,250,.9) 0%,rgba(250,250,250,0) 100%),
    radial-gradient(ellipse 120px 40px at 40% 55%,rgba(200,70,60,.35) 0%,rgba(200,70,60,0) 100%),
    linear-gradient(180deg,#eef2f4 0%,#cfdbe2 55%,#aebfca 100%)}
.hero-copy{position:absolute;left:64px;top:148px;width:360px}
.hero-copy h1{font-size:23px;font-weight:400;color:var(--teal);line-height:1.2;text-shadow:0 0 6px rgba(255,255,255,.9)}
.btn-dark{display:inline-block;margin-top:16px;background:var(--dark-btn);color:var(--white);font-size:9px;padding:7px 14px;border-radius:2px}
.hero-arrow{position:absolute;top:132px;width:20px;height:30px;background:rgba(60,66,71,.75);display:flex;align-items:center;justify-content:center}
.hero-arrow.left{left:0}.hero-arrow.right{right:0}
.features{display:flex;gap:15px;padding:14px 64px 0}
.feature{flex:1;height:226px;background:var(--sky);color:var(--white);text-align:center;padding:24px 16px}
.feature svg{width:64px;height:64px}
.feature h2{font-size:15px;font-weight:400;margin-top:30px}
.feature p{font-size:7.5px;line-height:1.45;margin-top:10px;opacity:.92}
.feature .more{font-size:7.5px;margin-top:12px;display:block}
.welcome{display:flex;gap:22px;padding:34px 64px 0}
.welcome-text{flex:1}
.welcome-text h2{font-size:19px;font-weight:600;color:var(--ink)}
.welcome-text p{font-size:8px;line-height:1.6;color:var(--muted);margin-top:12px}
.btn-sky{display:inline-block;margin-top:14px;background:var(--sky);color:var(--white);font-size:8px;padding:7px 18px}
.welcome-media{width:238px;height:176px;position:relative;
  background:
    radial-gradient(ellipse 40px 80px at 20% 65%,#ffffff 0%,rgba(255,255,255,0) 100%),
    radial-gradient(ellipse 40px 80px at 50% 70%,#ffffff 0%,rgba(255,255,255,0) 100%),
    radial-gradient(ellipse 40px 80px at 82% 65%,#ffffff 0%,rgba(255,255,255,0) 100%),
    radial-gradient(ellipse 130px 30px at 50% 8%,rgba(120,190,90,.55) 0%,rgba(120,190,90,0) 100%),
    linear-gradient(180deg,#e4ecef 0%,#cfdde3 100%)}
.play{position:absolute;left:104px;top:76px;width:30px;height:22px;border-radius:5px;background:#d8333a;display:flex;align-items:center;justify-content:center}
.products{position:absolute;left:0;top:880px;width:771px;height:256px;background:linear-gradient(#ffffff,var(--panel))}
.products h2{text-align:center;font-size:22px;font-weight:400;margin-top:6px}
.product-row{display:flex;justify-content:space-between;padding:20px 64px 0}
.product{width:196px;height:170px;background:
    radial-gradient(ellipse 80px 50px at 45% 55%,#ffffff 0%,rgba(255,255,255,0) 100%),
    linear-gradient(135deg,#f7f9fa 0%,#d6e8f0 60%,#9fd0e6 100%)}
.product.mid{background:
    radial-gradient(ellipse 70px 60px at 50% 50%,#ffffff 0%,rgba(255,255,255,0) 100%),
    linear-gradient(135deg,#f4f6f7 0%,#e0e6ea 60%,#c7d1d7 100%)}
.footer{position:absolute;left:0;top:1136px;width:771px;height:64px;background:var(--sky);color:var(--white);padding:14px 64px 0}
.footer-row{display:flex;justify-content:space-between;align-items:center}
.footer-nav{display:flex;gap:26px;font-size:9px}
.social{display:flex;gap:6px}
.social span{width:16px;height:16px;border-radius:50%;background:var(--white)}
.copyright{font-size:7px;margin-top:10px;opacity:.9}
</style>
</head>
<body>
<div class="topbar"><span>Call Now 01 234 5678 | Send a Message</span><span>Follow Us | Contact Us</span></div>
<header class="header">
  <div class="brand"><span class="brand-dot"></span><span class="brand-name">Compounding<br>Pharmacy</span></div>
  <nav class="nav"><span>Home</span><span>About us</span><span>Locations</span><span>Timings</span><span>Contact</span></nav>
</header>
<section class="hero">
  <div class="hero-photo" role="img" aria-label="Smiling pharmacist in a white coat in a bright pharmacy, colleague at the shelves behind"></div>
  <div class="hero-copy">
    <h1>Compounding... preparing customised medications for patients</h1>
    <span class="btn-dark">Read More</span>
  </div>
  <div class="hero-arrow left"><svg width="8" height="12" viewBox="0 0 8 12"><path d="M6 1L1 6l5 5" stroke="#fff" stroke-width="2" fill="none"/></svg></div>
  <div class="hero-arrow right"><svg width="8" height="12" viewBox="0 0 8 12"><path d="M2 1l5 5-5 5" stroke="#fff" stroke-width="2" fill="none"/></svg></div>
</section>
<section class="features">
  <article class="feature">
    <svg viewBox="0 0 70 70"><path d="M8 32h54c0 16-12 26-27 26S8 48 8 32z" fill="#fff"/><rect x="24" y="58" width="22" height="5" fill="#fff"/><path d="M40 30L58 8" stroke="#fff" stroke-width="7" stroke-linecap="round"/></svg>
    <h2>We do Compounding</h2>
    <p>Personalised medicines prepared in our purpose-built laboratory, tailored to each patient's needs with care.</p>
    <span class="more">Read more</span>
  </article>
  <article class="feature">
    <svg viewBox="0 0 70 70"><path d="M8 30L35 10l27 20" stroke="#fff" stroke-width="3" fill="none"/><rect x="14" y="30" width="42" height="32" stroke="#fff" stroke-width="3" fill="none"/><path d="M35 36v18M26 45h18" stroke="#fff" stroke-width="5"/></svg>
    <h2>Where we are</h2>
    <p>Visit our friendly local pharmacy in the heart of the community, with easy parking and a team ready to help.</p>
    <span class="more">Read more</span>
  </article>
  <article class="feature">
    <svg viewBox="0 0 70 70"><rect x="8" y="8" width="54" height="54" rx="6" fill="#fff"/><path d="M35 20v30M20 35h30" stroke="#6ccbe9" stroke-width="10"/></svg>
    <h2>When we are there</h2>
    <p>Open six days a week with extended evening hours, so patients, doctors and vet clients can reach us.</p>
    <span class="more">Read more</span>
  </article>
</section>
<section class="welcome">
  <div class="welcome-text">
    <h2>Welcome to Compounding Pharmacy</h2>
    <p>Compounding is the art of preparing medicines to suit the individual. For generations pharmacists made every remedy by hand, and today we bring that tradition together with modern standards, precise equipment and a dedicated preparation laboratory to create treatments that commercial products cannot always offer.</p>
    <p>We are committed to quality, safety and clear advice. Whether you are a patient, a prescriber or a veterinary client, our team will work with you to find the right strength, form and flavour for every need.</p>
    <span class="btn-sky">Read more</span>
  </div>
  <div class="welcome-media" role="img" aria-label="Video still of three pharmacy staff in white coats at the counter">
    <span class="play"><svg width="10" height="10" viewBox="0 0 10 10"><path d="M2 1l7 4-7 4z" fill="#fff"/></svg></span>
  </div>
</section>
<section class="products">
  <h2>Featured Products</h2>
  <div class="product-row">
    <div class="product" role="img" aria-label="Boxed medication product"></div>
    <div class="product mid" role="img" aria-label="Blister pack of capsules beside its box"></div>
    <div class="product" role="img" aria-label="Packaged compounded medicine"></div>
  </div>
</section>
<footer class="footer">
  <div class="footer-row">
    <nav class="footer-nav"><span>Home</span><span>About us</span><span>Locations</span><span>Timings</span><span>Contact</span></nav>
    <div class="social"><span></span><span></span><span></span><span></span></div>
  </div>
  <div class="copyright">© 2024 Compounding Pharmacy. All rights reserved.</div>
</footer>
</body>
</html>
```